Website for an electrical contractor :)

We are after a web site which can show pictures of our jobs and our capability in a professional, creative and easily understood way.

----- Brightvale Electrical ------

We really want a visually good looking website with three sections

Section one:
'Completed projects'
We have a few pictures of jobs which we've completed and would like to show off with a brief description. (see uploads)

Section two:
'Our capabilities'
Just a list of what services we offer

Section three:
We would like a 'contact us' section which people can send us a short msg and upload a file for plans to be able to send to us. We would need their name, phone number and email details. We would also need a short privacy policy saying 'we do not disclose information to third parties'.
We also want to display our contact number and postal address

Good luck :)

Target Market(s)

Adults 25 years+
Business owners
Builders
Real estate agents

Industry/Entity Type

Electrical

Colors

Designer to choose colors to be used in the design.

Requirements
Must have
• Visually appealing
Easy to understand
In the 'Completed projects' section, must have a list for each project we do i can upload pictures for it.

```html
<!DOCTYPE html>
<html lang="en">
<head>
<meta charset="utf-8">
<title>Brightvale Electrical</title>
<link href="https://fonts.googleapis.com/css2?family=Oswald:wght@400;500&family=Open+Sans:wght@400;600;700&display=swap" rel="stylesheet">
<style>
:root{
  --red:#d0102a;
  --ink:#222222;
  --muted:#555555;
  --white:#ffffff;
  --dark:#2b2f36;
  --sky:#5bd3f0;
  --footer:#1c1c1c;
}
*{margin:0;padding:0;box-sizing:border-box}
html,body{width:1200px;height:2590px;overflow:hidden;background:var(--white)}
body{position:relative;font-family:"Open Sans",sans-serif;color:var(--ink)}
.abs{position:absolute}

/* header */
.site-header{position:absolute;left:0;top:0;width:1200px;height:121px;background:var(--white)}
.brand{position:absolute;left:95px;top:36px;display:flex;align-items:center;gap:12px}
.brand-dot{width:30px;height:30px;border-radius:50%;background:var(--red)}
.brand-name{font-family:"Open Sans",sans-serif;font-size:38px;font-weight:400;color:#333;line-height:1}
.brand-sub{position:absolute;left:137px;top:86px;font-size:9px;color:#444;letter-spacing:.3px}
.main-nav{position:absolute;left:515px;top:54px;display:flex;gap:0}
.main-nav a{font-size:13px;letter-spacing:1px;color:#333;text-decoration:none;text-transform:uppercase;margin-right:54px;padding-bottom:8px}
.main-nav a.active{color:var(--red);border-bottom:2px solid var(--red)}

/* hero */
.hero{position:absolute;left:0;top:121px;width:1200px;height:614px;background:linear-gradient(180deg,#4a86d6 0%,#8ab5e6 30%,#6b6862 55%,#3a3a3c 100%)}
.hero-caption{position:absolute;left:0;top:233px;width:1200px;height:173px;background:rgba(40,40,40,.72);display:flex;flex-direction:column;justify-content:center;align-items:center}
.hero-caption p{font-family:"Oswald",sans-serif;font-weight:400;font-size:38px;line-height:52px;color:var(--white)}
.hero-arrow{position:absolute;top:268px}
.hero-dots{position:absolute;left:572px;top:584px;display:flex;gap:5px}
.hero-dots span{width:9px;height:9px;border-radius:50%;border:1px solid rgba(255,255,255,.8)}
.hero-dots span.on{background:var(--white)}

/* projects */
.projects{position:absolute;left:0;top:735px;width:1200px;height:483px;background:linear-gradient(180deg,#3d4450 0%,#2a2d33 60%,#3a3b3e 100%)}
.section-title{font-family:"Oswald",sans-serif;font-weight:400;font-size:34px;text-align:center;text-transform:uppercase;position:absolute;left:0;width:1200px}
.section-title em{font-style:normal;color:var(--red)}
.projects .section-title{top:44px;color:var(--white)}
.project-card{position:absolute;top:122px;width:317px}
.project-photo{width:317px;height:176px;border:3px solid var(--white)}
.project-card h3{font-family:"Oswald",sans-serif;font-weight:400;font-size:21px;color:var(--white);margin-top:18px;text-transform:uppercase}
.project-card p{font-size:14px;line-height:25px;color:#eeeeee;margin-top:6px}

/* capabilities */
.capabilities{position:absolute;left:0;top:1218px;width:1200px;height:654px;background:var(--white)}
.capabilities .section-title{top:42px;color:var(--ink)}
.capability-visual{position:absolute;left:100px;top:108px;width:242px;height:491px;background:linear-gradient(180deg,#e9e4dc 0%,#6d6f72 40%,#9a9590 75%,#e9e4dc 100%)}
.capability-col{position:absolute;top:152px}
.capability-col h4{font-size:19px;font-weight:600;color:var(--red);letter-spacing:1px;text-transform:uppercase;margin-bottom:14px}
.capability-col li{list-style:none;font-size:14px;line-height:35px;color:#333;letter-spacing:.4px}
.capability-col li::before{content:"»";color:var(--red);font-weight:700;margin-right:10px}

/* contact */
.contact{position:absolute;left:0;top:1872px;width:1200px;height:398px;background:linear-gradient(180deg,#5c5c5c,#3e3e3e)}
.contact .heading{position:absolute;left:93px;top:44px;font-family:"Oswald",sans-serif;font-size:31px;color:var(--white);text-transform:uppercase}
.contact .heading em{font-style:normal;color:var(--red)}
.field{position:absolute;left:93px;width:456px;height:50px;background:#c9c9c9;border:1px solid #dddddd;font-size:14px;color:#333;padding:14px 13px}
.send{position:absolute;left:93px;top:290px;width:119px;height:38px;background:var(--red);color:var(--white);font-size:14px;font-weight:600;text-align:center;line-height:38px}
.map{position:absolute;left:618px;top:45px;width:492px;height:297px;background:linear-gradient(135deg,#e8e8e8,#cfcfcf)}
.map-card{position:absolute;left:206px;top:90px;width:180px;height:110px;background:var(--white);border:1px solid #999;padding:12px 22px;font-size:11px;line-height:19px;font-weight:600;color:#333}
.map-card strong{display:block;color:#2a6fb5;font-weight:600;margin-bottom:6px}

/* feed */
.feed{position:absolute;left:0;top:2270px;width:1200px;height:150px;background:var(--sky)}
.feed-brand{position:absolute;left:100px;top:56px;display:flex;align-items:center;gap:12px;font-size:31px;font-weight:700;color:var(--white)}
.feed-brand span.mark{width:34px;height:34px;border-radius:50%;background:var(--white)}
.feed-divider{position:absolute;left:297px;top:30px;width:1px;height:90px;background:rgba(255,255,255,.7)}
.feed-text{position:absolute;left:326px;top:46px;width:790px;font-size:15px;line-height:27px;color:#1f3b4a}
.feed-arrows{position:absolute;left:1052px;top:100px}

/* footer */
.site-footer{position:absolute;left:0;top:2420px;width:1200px;height:170px;background:var(--footer)}
.footer-links{position:absolute;left:92px;top:68px;font-size:12px;color:var(--white);letter-spacing:.3px}
.footer-copy{position:absolute;left:92px;top:92px;font-size:12px;color:var(--white)}
.social-label{position:absolute;left:748px;top:68px;font-size:12px;color:var(--white)}
.social-sub{position:absolute;left:748px;top:92px;font-size:11px;color:var(--white)}
.social-icons{position:absolute;left:944px;top:62px;display:flex;gap:11px}
.social-icons span{width:34px;height:34px;border-radius:50%;border:2px solid var(--white);background:#7a7a7a}
</style>
</head>
<body>

<header class="site-header">
  <div class="brand"><span class="brand-dot"></span><span class="brand-name">Brightvale</span></div>
  <div class="brand-sub">Electrical &amp; Communications &nbsp; EC1234</div>
  <nav class="main-nav">
    <a class="active">Home</a><a>About</a><a>Services</a><a>News</a><a>Blog</a><a>Contact</a>
  </nav>
</header>

<section class="hero" role="img" aria-label="Photo of a completed brick residential building with paved driveway under blue sky">
  <div class="hero-caption">
    <p>Fusce dapibus tellus ac cursus commodo.</p>
    <p>Duis mollis est non commodo luctus, nisi erat porttitor.</p>
  </div>
  <svg class="hero-arrow" style="left:58px" width="28" height="70" viewBox="0 0 28 70"><polyline points="26,2 2,35 26,68" fill="none" stroke="#fff" stroke-width="2"/></svg>
  <svg class="hero-arrow" style="left:1116px" width="28" height="70" viewBox="0 0 28 70"><polyline points="2,2 26,35 2,68" fill="none" stroke="#fff" stroke-width="2"/></svg>
  <div class="hero-dots"><span></span><span></span><span class="on"></span><span></span><span></span></div>
</section>

<section class="projects">
  <h2 class="section-title">Completed <em>Projects</em></h2>
  <article class="project-card" style="left:90px">
    <div class="project-photo" role="img" aria-label="Photo of a new concrete commercial building" style="background:linear-gradient(180deg,#2d5fb8 0%,#7fa5e0 35%,#d8d6d0 60%,#b9b5ad 100%)"></div>
    <h3>Ipsum is simply dummy text</h3>
    <p>Lorem Ipsum has been the industry's standard dummy text ever since the 1500s, when an</p>
  </article>
  <article class="project-card" style="left:437px">
    <div class="project-photo" role="img" aria-label="Photo of an empty warehouse interior with overhead lighting" style="background:linear-gradient(180deg,#4a4a4a 0%,#7a7772 45%,#3a3836 100%)"></div>
    <h3>Ipsum is simply dummy text</h3>
    <p>Lorem Ipsum has been the industry's standard dummy text ever since the 1500s, when an</p>
  </article>
  <article class="project-card" style="left:786px">
    <div class="project-photo" role="img" aria-label="Photo of a switchboard with wired circuit breakers" style="background:linear-gradient(135deg,#8b3b3b 0%,#c9c3bd 50%,#7a2a2a 100%)"></div>
    <h3>Ipsum is simply dummy text</h3>
    <p>Lorem ipsum dolor sit amet, consectetur adipiscing elit. Sed blandit massa</p>
  </article>
</section>

<section class="capabilities">
  <h2 class="section-title">Our <em>Capabilities</em></h2>
  <div class="capability-visual" role="img" aria-label="Smartphone showing a photo of a lit commercial interior"></div>
  <div class="capability-col" style="left:418px">
    <h4>Residential</h4>
    <ul>
      <li>24hr Support / faults</li>
      <li>RCD (Safety Switch) installations</li>
      <li>Smoke alarms</li>
      <li>Power points</li>
      <li>Lighting points</li>
      <li>External lighting</li>
      <li>Sensor lighting</li>
      <li>Switching</li>
      <li>Antennas and Arial points</li>
      <li>Dimmers</li>
      <li>Ceiling fans</li>
    </ul>
  </div>
  <div class="capability-col" style="left:788px">
    <h4>Commercial / Industrial</h4>
    <ul>
      <li>24hr Support / faults</li>
      <li>Lighting/power design and consultation</li>
      <li>Commercial lighting</li>
      <li>Emergency and exit lighting</li>
      <li>Led strip lighting</li>
      <li>Energy efficient lighting</li>
      <li>Temporary lighting</li>
      <li>Illuminated signage</li>
      <li>Switchboard relocations</li>
      <li>Maintenance</li>
      <li>RCD installation</li>
    </ul>
  </div>
</section>

<section class="contact" role="region" aria-label="Contact us; background shows a faded street map">
  <h2 class="heading">Contact <em>Us</em></h2>
  <div class="field" style="top:99px">Your Name</div>
  <div class="field" style="top:161px">Your Phone</div>
  <div class="field" style="top:226px">Your Email</div>
  <div class="send">SEND</div>
  <div class="map" role="img" aria-label="Street map showing the office location">
    <svg class="abs" style="left:156px;top:82px" width="34" height="46" viewBox="0 0 34 46"><path d="M17 0C7.6 0 0 7.4 0 16.6 0 29 17 46 17 46S34 29 34 16.6C34 7.4 26.4 0 17 0z" fill="#e53935"/><circle cx="17" cy="16" r="6" fill="#fff"/></svg>
    <div class="map-card"><strong>PLACE TITLE HERE</strong>222 2ND AVE N<br>SOMEPLACE, WD A1B2C3<br>(111) 222-33</div>
  </div>
</section>

<section class="feed">
  <div class="feed-brand"><span class="mark"></span>Chirpline</div>
  <div class="feed-divider"></div>
  <p class="feed-text">Sed ut perspiciatis unde omnis iste natus error sit voluptatem accusantium doloremque laudantium, totam rem aperiam, eaque ipsa quae ab illo inventore veritatis et quasi architecto beatae vitae dicta sunt</p>
  <svg class="feed-arrows" width="30" height="16" viewBox="0 0 30 16"><polyline points="8,2 3,8 8,14" fill="none" stroke="#1f3b4a" stroke-width="2"/><polyline points="22,2 27,8 22,14" fill="none" stroke="#fff" stroke-width="2"/></svg>
</section>

<footer class="site-footer">
  <div class="footer-links">HOME &nbsp;|&nbsp; ABOUT &nbsp;|&nbsp; NEWS &nbsp;|&nbsp; BLOG &nbsp;|&nbsp; CONTACTS</div>
  <div class="footer-copy">Copyrights © 2015 &nbsp;|&nbsp; Privacy Policy</div>
  <div class="social-label">SOCIAL NETWORKS</div>
  <div class="social-sub">Lorem Ipsum is simply dummy text</div>
  <div class="social-icons" aria-label="Social network links"><span></span><span></span><span></span><span></span></div>
</footer>

</body>
</html>
```